Detail Shop Business card design

i need a business card design for my new detailing company called 'Brisk's Polish Works'. i want an all black and white design . simple, direct and to the point. i want the designer to choose a fitting font to match the logothe front should have logo, address, phone and email and the back side should have a slogan and text indicating that we offer services on anything including cars, trucks, motorcycles and RVs. slogan will read "we take pride in your ride"
maybe also very small on the back side the IG icon with Brisks_Polish_Works

phone 208.417.6352
address 3847 E Larkin Ave
Spokane WA 99214
email: BrisksPolish@mailvexo.com

Target Market(s)

all ages , auto enthusiasts

Industry/Entity Type

Automotive

Contact Information for Business Card

the front should have logo, address, phone and email and the back side should have a slogan and text indicating that we offer services on anything including cars, trucks, motorcycles and RVs. slogan will read "we take pride in your ride"

phone 208.417.6352
address 3847 E Larkin Ave
Spokane WA 99214

Colors
000000
ffffff

Requirements
Must have
• bold font and very simple design with good spacing
Nice to have
• anything creative from the designer indicating we service any types of vehicles
Should not have
• any colors ,

```html
<!DOCTYPE html>
<html lang="en">
<head>
<meta charset="utf-8">
<title>Brisk's Polish Works — Business Card</title>
<link rel="stylesheet" href="https://fonts.googleapis.com/css2?family=PT+Serif:ital,wght@0,700;1,700&display=swap">
<style>
  :root {
    --ink: #000000;
    --paper: #ffffff;
    --stage: #2b2c2f;
    --card-w: 560px;
    --card-h: 320px;
  }
  * { box-sizing: border-box; margin: 0; padding: 0; }
  html, body { width: 1200px; height: 900px; overflow: hidden; }
  body {
    background: var(--stage);
    font-family: "PT Serif", Georgia, serif;
    display: flex;
    flex-direction: column;
    align-items: center;
    justify-content: center;
    gap: 60px;
  }
  .card {
    position: relative;
    width: var(--card-w);
    height: var(--card-h);
    border-radius: 22px;
    overflow: hidden;
  }
  .card-shape { position: absolute; inset: 0; }

  /* Front */
  .card-front { background: var(--paper); }
  .brand {
    position: absolute;
    left: 34px;
    top: 70px;
    display: flex;
    align-items: center;
    gap: 12px;
    color: var(--ink);
    font-weight: 700;
    font-style: italic;
    font-size: 26px;
    line-height: 1.1;
  }
  .brand-dot {
    width: 16px; height: 16px;
    border-radius: 50%;
    background: var(--ink);
    flex: none;
  }
  .contact {
    position: absolute;
    left: 306px;
    top: 150px;
    color: var(--paper);
    font-style: italic;
    font-weight: 700;
    font-size: 17px;
    line-height: 1.45;
  }
  .contact-rule {
    width: 120px;
    height: 2px;
    background: var(--paper);
    margin: 12px 0 12px 40px;
  }

  /* Back */
  .card-back { background: var(--ink); }
  .slogan-band {
    position: absolute;
    left: 0; right: 0;
    top: 46px;
    height: 72px;
    background: var(--paper);
    display: flex;
    align-items: center;
    justify-content: center;
    color: var(--ink);
    font-weight: 700;
    font-style: italic;
    font-size: 28px;
    text-transform: uppercase;
    letter-spacing: 0.5px;
  }
  .band-line {
    position: absolute;
    left: 0; right: 0;
    height: 3px;
    background: var(--paper);
  }
  .band-line-top { top: 34px; }
  .band-line-bottom { top: 127px; }
  .services {
    position: absolute;
    left: 28px;
    bottom: 56px;
    display: flex;
    align-items: center;
    gap: 14px;
  }
  .vehicle-icon { width: 46px; height: 28px; }
  .back-divider {
    position: absolute;
    left: 290px;
    bottom: 44px;
    width: 2px;
    height: 52px;
    background: var(--paper);
  }
  .social {
    position: absolute;
    left: 316px;
    bottom: 58px;
    display: flex;
    align-items: center;
    gap: 8px;
    color: var(--paper);
    font-style: italic;
    font-weight: 700;
    font-size: 17px;
  }
  .social-mark {
    width: 14px; height: 14px;
    border-radius: 50%;
    background: var(--paper);
    flex: none;
  }
</style>
</head>
<body>

<section class="card card-front" aria-label="Card front">
  <svg class="card-shape" viewBox="0 0 560 320" width="560" height="320" aria-hidden="true">
    <polygon points="0,262 200,262 290,120 560,120 560,320 0,320" fill="#000000"/>
    <polyline points="0,276 208,276 298,134 560,134" fill="none" stroke="#ffffff" stroke-width="2"/>
  </svg>
  <div class="brand"><span class="brand-dot"></span><span>Brisk's<br>Polish Works</span></div>
  <div class="contact">
    <p class="contact-phone">208.417.6352</p>
    <p class="contact-email">BrisksPolish@mailvexo.com</p>
    <div class="contact-rule"></div>
    <p class="contact-street">3847 E Larkin Ave</p>
    <p class="contact-city">Spokane WA 99214</p>
  </div>
</section>

<section class="card card-back" aria-label="Card back">
  <div class="band-line band-line-top"></div>
  <div class="slogan-band">We take pride in your ride</div>
  <div class="band-line band-line-bottom"></div>

  <div class="services" aria-label="Trucks, cars, motorcycles and RVs">
    <svg class="vehicle-icon" viewBox="0 0 46 28" aria-hidden="true">
      <rect x="2" y="6" width="28" height="14" fill="#fff"/>
      <path d="M31 10h7l5 5v5H31z" fill="#fff"/>
      <circle cx="10" cy="22" r="4" fill="#fff" stroke="#000" stroke-width="1.5"/>
      <circle cx="37" cy="22" r="4" fill="#fff" stroke="#000" stroke-width="1.5"/>
    </svg>
    <svg class="vehicle-icon" viewBox="0 0 46 28" aria-hidden="true">
      <path d="M4 20v-5l6-2 6-6h14l7 6 5 1v6z" fill="#fff"/>
      <circle cx="12" cy="21" r="4" fill="#fff" stroke="#000" stroke-width="1.5"/>
      <circle cx="35" cy="21" r="4" fill="#fff" stroke="#000" stroke-width="1.5"/>
    </svg>
    <svg class="vehicle-icon" viewBox="0 0 46 28" aria-hidden="true">
      <circle cx="10" cy="19" r="6" fill="none" stroke="#fff" stroke-width="3"/>
      <circle cx="36" cy="19" r="6" fill="none" stroke="#fff" stroke-width="3"/>
      <path d="M10 19l8-8h10l8 8M24 11l4-5h5" fill="none" stroke="#fff" stroke-width="3"/>
    </svg>
    <svg class="vehicle-icon" viewBox="0 0 46 28" aria-hidden="true">
      <rect x="2" y="3" width="30" height="17" fill="#fff"/>
      <path d="M33 9h6l5 5v6H33z" fill="#fff"/>
      <circle cx="11" cy="22" r="4" fill="#fff" stroke="#000" stroke-width="1.5"/>
      <circle cx="37" cy="22" r="4" fill="#fff" stroke="#000" stroke-width="1.5"/>
    </svg>
  </div>
  <div class="back-divider"></div>
  <div class="social"><span class="social-mark"></span><span>Brisks_Polish_Works</span></div>
</section>

</body>
</html>
```